Venture 482 - Lumora Book Cover

I am looking for a Lumora book cover for my book about "Venture 482".
The Book is Titled:
Venture 482 Ascended
Shaping Outcomes: Paths To Unlocking Cosmic Truths
Author is Dorian Pell
Here is a book description that may help you understand more about it:
Inspired by the genius of Edwin Marlowe, this comprehensive guide delves into the ancient wisdom and cutting-edge science behind the 482 method, a powerful tool for manifesting your desires. Whether you're seeking personal growth, financial success, or spiritual enlightenment, this book provides advanced techniques and methods to transform your dreams into reality.
Any questions please ask.
Thanks
Owen

```html
<!DOCTYPE html>
<html lang="en">
<head>
<meta charset="utf-8">
<title>Venture 482 Ascended — Dorian Pell</title>
<link rel="stylesheet" href="https://fonts.googleapis.com/css2?family=Cinzel:wght@400&family=Libre+Franklin:wght@800&family=Fraunces:opsz,wght@144,800&family=Montserrat:wght@400;700&display=swap">
<style>
  :root {
    --page-bg: #e9e8e6;
    --sky-top: #0f1a26;
    --sky-mid: #2a4560;
    --sky-low: #4d6f92;
    --scene-top: #6f8fb0;
    --scene-mid: #b9c4cc;
    --scene-low: #8a8a78;
    --cream: #f6e9dc;
    --gold: #d9c257;
    --white: #f4f6f8;
  }
  * { margin: 0; padding: 0; box-sizing: border-box; }
  html, body {
    width: 1200px; height: 1131px; overflow: hidden;
    background: var(--page-bg);
  }
  .cover {
    position: absolute; left: 229px; top: 10px;
    width: 742px; height: 1111px;
    overflow: hidden;
    text-align: center;
  }
  .cover-sky {
    position: absolute; inset: 0;
    background: linear-gradient(180deg, var(--sky-top) 0%, var(--sky-mid) 35%, var(--sky-low) 62%, var(--scene-top) 100%);
  }
  .cover-scene {
    position: absolute; left: 0; right: 0; top: 626px; bottom: 0;
    background: linear-gradient(180deg, rgba(111,143,176,0) 0%, var(--scene-mid) 40%, var(--scene-low) 100%);
  }
  .author {
    position: absolute; left: 0; right: 0; top: 74px;
    font-family: "Cinzel", serif; font-weight: 400;
    font-size: 36px; letter-spacing: 0.32em;
    color: var(--cream);
  }
  .title-top {
    position: absolute; left: 0; right: 0; top: 150px;
    font-family: "Libre Franklin", sans-serif; font-weight: 800;
    font-size: 72px; letter-spacing: -0.02em;
    color: var(--cream);
    text-shadow: 0 3px 6px rgba(0,0,0,0.35);
  }
  .title-number {
    position: absolute; left: 0; right: 0; top: 210px;
    font-family: "Fraunces", serif; font-weight: 800;
    font-size: 190px; line-height: 1; letter-spacing: -0.03em;
    color: var(--gold);
    text-shadow: 0 4px 8px rgba(0,0,0,0.35);
  }
  .title-edition {
    position: absolute; left: 0; right: 0; top: 412px;
    font-family: "Montserrat", sans-serif; font-weight: 700;
    font-size: 38px; letter-spacing: 0.42em; padding-left: 0.42em;
    color: var(--gold);
  }
  .subtitle-lead {
    position: absolute; left: 0; right: 0; top: 478px;
    font-family: "Montserrat", sans-serif; font-weight: 400;
    font-size: 28px; letter-spacing: 0.02em;
    color: var(--white);
  }
  .subtitle-rest {
    position: absolute; left: 0; right: 0; top: 520px;
    font-family: "Montserrat", sans-serif; font-weight: 400;
    font-size: 26px; line-height: 1.3;
    color: var(--white);
  }
</style>
</head>
<body>
  <main class="cover">
    <div class="cover-sky" role="img" aria-label="Dark blue sky with drifting clouds and a small flock of birds"></div>
    <div class="cover-scene" role="img" aria-label="Open doorway in the clouds revealing a sunlit city skyline of tall towers"></div>
    <p class="author">DORIAN PELL</p>
    <h1>
      <span class="title-top">VENTURE</span>
      <span class="title-number">482</span>
      <span class="title-edition">ASCENDED</span>
    </h1>
    <p class="subtitle-lead">SHAPING OUTCOMES:</p>
    <p class="subtitle-rest">Paths to unlocking<br>cosmic truths</p>
  </main>
</body>
</html>
```